Corvellan - online education agent and consultancy

Online education provider for business to business market needs a dynamic, modern and mobile friendly website. We have the shell view www.quorvana.com but it is boring!
I will need to add courses to the website - Business, Health and Wellbeing, Digital, Aviation.
I am targeting mainly services based industries - so blue collar workers, living in the outer suburbs, will be studying online and most likely from home.
They need to feel safe and secure - we are reputable and importantly can support them all the way to course completion.
What makes us stand out from everyone else - we dont offer any courses - we pick and choose the best courses, with the best providers and only offer quality.
We take the time to find out what the student really wants to achieve and match them with the right education provider.

Target Market(s)

Business to Business - HR managers, People and Culture Managers, employees who are 25+ years currently working wanting to further their careers with accredited qualifications

Industry/Entity Type

Education

Number of Pages Required

5+ page

Font styles to use
Sans Serif

Colors
00a990
acd036
0792cd
a54499
f37122

Requirements
Must have
• Mobile functionality - view on ovulet/ovutab
• Home page
• Courses section
• Contact us
• Payment checkout to be added
Nice to have
• Fresh, inviting, images that reflect the difference we will make - supporting people through the whole journey.
• It needs to be inviting - homely but modern
Should not have
• Black, dark colours

```html
<!DOCTYPE html>
<html lang="en">
<head>
<meta charset="utf-8">
<title>Quillaby – Online Education Agent</title>
<link href="https://fonts.googleapis.com/css2?family=Open+Sans:wght@400;600;700&family=Roboto:wght@400;500;700&display=swap" rel="stylesheet">
<style>
:root{
  --teal:#00a990;
  --lime:#acd036;
  --blue:#0792cd;
  --purple:#a54499;
  --orange:#f37122;
  --green:#5cb85c;
  --text:#555c63;
  --muted:#8a9096;
  --light:#f2f4f5;
  --line:#e3e6e8;
  --white:#ffffff;
}
*{box-sizing:border-box;margin:0;padding:0}
html,body{width:1200px;height:2312px;overflow:hidden}
body{font-family:"Open Sans",Arial,sans-serif;color:var(--text);background:var(--white);position:relative}
.site-header{position:absolute;top:0;left:0;width:1200px;height:120px;background:var(--white)}
.brand{position:absolute;left:70px;top:28px;display:flex;align-items:center;gap:12px;font-family:"Roboto",sans-serif;font-weight:700;font-size:44px;color:var(--lime);letter-spacing:1px}
.brand-dot{width:18px;height:18px;border-radius:50%;background:var(--orange)}
.topline{position:absolute;right:70px;top:14px;display:flex;align-items:center;gap:10px;font-size:14px;color:var(--muted)}
.social{width:18px;height:18px;border-radius:50%;background:var(--teal)}
.main-nav{position:absolute;right:60px;top:62px;display:flex}
.main-nav a{display:block;padding:14px 18px;font-family:"Roboto",sans-serif;font-size:14px;font-weight:500;color:var(--text);text-decoration:none}
.main-nav a.active{background:var(--teal);color:var(--white)}
.hero{position:absolute;top:120px;left:0;width:1200px;height:660px;background:linear-gradient(180deg,#7fb4d8 0%,#8fb37a 55%,#5f8a3e 100%)}
.hero-copy{position:absolute;top:240px;width:100%;text-align:center;color:var(--white)}
.hero-copy h1{font-family:"Roboto",sans-serif;font-weight:700;font-size:46px;letter-spacing:1px}
.hero-copy p{font-size:16px;margin-top:8px;line-height:1.5}
.hero-btn{display:inline-block;margin-top:14px;background:var(--orange);color:var(--white);font-size:13px;font-weight:600;padding:10px 22px;border-radius:3px}
.features{position:absolute;top:560px;left:168px;display:flex;gap:24px}
.feature{width:272px;height:270px;padding:96px 22px 0;text-align:center;color:var(--white);position:relative;box-shadow:0 6px 14px rgba(0,0,0,.15)}
.feature.blue{background:var(--blue)}.feature.orange{background:var(--orange)}.feature.green{background:var(--green)}
.feature-icon{position:absolute;top:-8px;left:96px;width:80px;height:80px;border-radius:50%;background:var(--white);display:flex;align-items:center;justify-content:center}
.feature h3{font-family:"Roboto",sans-serif;font-size:20px;font-weight:700}
.feature p{font-size:12px;line-height:1.6;margin-top:8px}
.btn-ghost{display:inline-block;margin-top:14px;background:var(--white);color:var(--text);font-size:11px;font-weight:700;padding:7px 16px;border-radius:2px}
.welcome{position:absolute;top:880px;left:0;width:1200px;text-align:center}
.welcome h2{font-family:"Roboto",sans-serif;font-size:36px;font-weight:700;color:var(--text)}
.welcome h2 span{color:var(--lime)}
.welcome p{width:1000px;margin:20px auto 0;font-size:13px;line-height:1.7;color:var(--muted)}
.btn-solid{display:inline-block;margin-top:22px;background:var(--green);color:var(--white);font-size:12px;font-weight:700;padding:12px 22px;border-radius:3px}
.online{position:absolute;top:1150px;left:0;width:1200px;height:430px;display:flex}
.online-copy{width:600px;background:var(--teal);color:var(--white);padding:70px 60px 0 80px}
.online-copy h2{font-family:"Roboto",sans-serif;font-size:28px;font-weight:500}
.online-copy ul{list-style:none;margin-top:20px}
.online-copy li{font-size:13px;line-height:1.5;margin-bottom:10px;padding-left:22px;position:relative}
.online-copy li::before{content:"";position:absolute;left:0;top:5px;width:9px;height:9px;border-radius:50%;background:var(--white)}
.btn-outline{display:inline-block;margin-top:12px;border:2px solid var(--white);font-size:12px;font-weight:700;padding:9px 20px}
.online-art{width:600px;background:var(--light);display:flex;align-items:center;justify-content:center}
.online-art div{width:360px;height:300px;border-radius:8px;background:linear-gradient(160deg,#cfd6da,#8e979d)}
.news{position:absolute;top:1620px;left:80px;width:1040px}
.news h2{font-family:"Roboto",sans-serif;font-size:26px;font-weight:700}
.news-grid{display:flex;gap:40px;margin-top:24px}
.news-item{display:flex;gap:22px;width:500px}
.news-photo{width:230px;height:170px;flex:none}
.news-item h4{font-size:13px;font-weight:700;color:var(--text)}
.news-date{font-size:12px;color:var(--orange);margin:6px 0}
.news-item p{font-size:12px;line-height:1.6;color:var(--muted)}
.btn-small{display:inline-block;margin-top:10px;border:1px solid var(--line);font-size:10px;padding:6px 12px;color:var(--muted)}
.site-footer{position:absolute;top:2000px;left:0;width:1200px;height:268px;background:var(--light);padding:36px 80px 0;display:flex;gap:50px}
.site-footer h5{font-size:17px;font-weight:600;color:var(--text);margin-bottom:12px}
.col-news{width:300px}.col-news p{font-size:12px;line-height:1.5;color:var(--muted)}
.subscribe{display:flex;margin-top:14px}
.subscribe span{flex:1;height:36px;background:var(--white);border:1px solid var(--line);font-size:11px;color:var(--muted);padding:10px}
.subscribe b{background:var(--teal);color:var(--white);font-size:11px;padding:11px 14px}
.col-contact{width:240px;font-size:12px;color:var(--muted);line-height:1.9}
.col-contact .brand{position:static;font-size:30px;margin-bottom:8px}
.col-links{width:160px}.col-links li{list-style:none;font-size:12px;color:var(--muted);line-height:1.9}
.col-tweets{width:240px}
.tweet{display:flex;gap:10px;font-size:11px;color:var(--muted);line-height:1.5;margin-bottom:10px}
.tweet i{width:16px;height:16px;flex:none;background:var(--text);border-radius:2px;margin-top:2px}
.copyright{position:absolute;top:2268px;left:0;width:1200px;height:44px;background:var(--teal);color:var(--white);font-size:12px;text-align:center;line-height:44px}
</style>
</head>
<body>
<header class="site-header">
  <div class="brand">Quillaby<span class="brand-dot"></span></div>
  <div class="topline">+0044 555 0192 <span class="social"></span><span class="social"></span><span class="social"></span></div>
  <nav class="main-nav">
    <a class="active">HOME</a><a>ABOUT US</a><a>CORVELLAN</a><a>RESEARCH</a><a>COURSES</a><a>CONTACT US</a>
  </nav>
</header>

<section class="hero" role="img" aria-label="Photo of a group of happy students jumping on a grassy field">
  <div class="hero-copy">
    <h1>ONLINE EDUCATION AGENT</h1>
    <p>We match working adults with the best accredited courses<br>and support them all the way to completion.</p>
    <span class="hero-btn">GET STARTED</span>
  </div>
</section>

<div class="features">
  <article class="feature blue">
    <div class="feature-icon"><svg width="40" height="40" viewBox="0 0 44 44"><circle cx="22" cy="18" r="12" fill="none" stroke="#0792cd" stroke-width="3"/><rect x="16" y="31" width="12" height="6" fill="#0792cd"/></svg></div>
    <h3>CORVELLAN</h3>
    <p>We choose the best providers so you only study quality courses that employers value and trust.</p>
    <span class="btn-ghost">READ MORE</span>
  </article>
  <article class="feature orange">
    <div class="feature-icon"><svg width="44" height="36" viewBox="0 0 48 40"><polygon points="24,4 46,14 24,24 2,14" fill="#f37122"/><path d="M12 19v9c6 5 18 5 24 0v-9l-12 6z" fill="#f37122"/></svg></div>
    <h3>ACCREDITED COURSES</h3>
    <p>Business, health and wellbeing, digital and aviation courses with recognised qualifications.</p>
    <span class="btn-ghost">READ MORE</span>
  </article>
  <article class="feature green">
    <div class="feature-icon"><svg width="40" height="36" viewBox="0 0 44 40"><path d="M4 6h36v22H18l-9 8v-8H4z" fill="#5cb85c"/></svg></div>
    <h3>LET'S CHAT</h3>
    <p>Tell us what you want to achieve and our advisors will help you pick the right path today.</p>
    <span class="btn-ghost">READ MORE</span>
  </article>
</div>

<section class="welcome">
  <h2>WELCOME TO <span>QUILLABY</span></h2>
  <p>Corvellan is a unique program that has been specifically crafted to provide the best learning outcome for your employees. We commence our relationship with you and your team to understand what you need, then we find the right accredited provider for each learner. Our student support, mentors and development programs ensure every person finishes their course with confidence and new skills they can use at work straight away.</p>
  <span class="btn-solid">REQUEST A QUOTE</span>
</section>

<section class="online">
  <div class="online-copy">
    <h2>ONLINE EDUCATION</h2>
    <ul>
      <li>We offer accredited education courses from a range of trusted institutions that are known for quality.</li>
      <li>We work to your budget and time.</li>
      <li>At Corvellan we take the time to understand what you want to achieve and match you with the right provider.</li>
      <li>We work with universities, TAFE and private providers.</li>
      <li>Earn certificates, diplomas and degrees — we are with you until the course is complete.</li>
    </ul>
    <span class="btn-outline">READ MORE INFO</span>
  </div>
  <div class="online-art"><div role="img" aria-label="Illustration of a computer monitor with a graduation cap, books and pencils"></div></div>
</section>

<section class="news">
  <h2>LATEST NEWS</h2>
  <div class="news-grid">
    <article class="news-item">
      <div class="news-photo" role="img" aria-label="Photo of students celebrating outdoors" style="background:linear-gradient(160deg,#9cc3e0,#6f9a4f)"></div>
      <div><h4>LOREM IPSUM DOLOR SIT AMET,</h4><div class="news-date">July 28, 2016</div><p>New health and wellbeing courses now open for enrolment with flexible online study options.</p><span class="btn-small">READ MORE</span></div>
    </article>
    <article class="news-item">
      <div class="news-photo" role="img" aria-label="Photo of colourful pencils and study supplies" style="background:linear-gradient(160deg,#e8c27a,#7fae5a)"></div>
      <div><h4>LOREM IPSUM DOLOR SIT AMET,</h4><div class="news-date">July 28, 2016</div><p>Learn how our advisors support working students from first enquiry right through to graduation.</p><span class="btn-small">READ MORE</span></div>
    </article>
  </div>
</section>

<footer class="site-footer">
  <div class="col-news">
    <h5>Sign up for newsletter</h5>
    <p>Receive our latest course news and study tips straight to your inbox each month.</p>
    <div class="subscribe"><span>Enter Email</span><b>SUBSCRIBE</b></div>
  </div>
  <div class="col-contact">
    <div class="brand">Quillaby<span class="brand-dot"></span></div>
    <div>Larkfield, Eastvale Region</div>
    <div>Call us: +0044 555 0192</div>
    <div>info@quorvana.com</div>
  </div>
  <div class="col-links">
    <h5>Quick Links</h5>
    <ul><li>Home</li><li>Corvellan</li><li>Research</li><li>Courses</li><li>Contact</li></ul>
  </div>
  <div class="col-tweets">
    <h5>Latest Tweet's</h5>
    <div class="tweet"><i></i><span>New aviation course intake opens next month, enquire now. — 1 day ago</span></div>
    <div class="tweet"><i></i><span>Congratulations to all our recent graduates this season! — 3 days ago</span></div>
  </div>
</footer>
<div class="copyright">© 2016 quorvana.com, All Rights Reserved.</div>
</body>
</html>
```